Quellrow Capital LLC

Need Professional Business cards for New Investment Fund

Target Market(s)

High Quality investors

Industry/Entity Type

Financial

Contact Information for Business Card

Phone Number +1 555 284 6190
Name Lukas Varenko
Title Fund Manager
email lv@FundQuellrow.com
Website www.FundQuellrow.com

Colors

Designer to choose colors to be used in the design.

Requirements
Must have
• Must have our Logo and all of the above. Must be made so lettering and loge can be raised

```html
<!DOCTYPE html>
<html lang="en">
<head>
<meta charset="utf-8">
<title>Quellrow Capital – Business Card</title>
<link href="https://fonts.googleapis.com/css2?family=Teko:wght@500;600&family=Arimo:wght@400;700&display=swap" rel="stylesheet">
<style>
  :root {
    --backdrop: #2b2b2b;
    --card: #232323;
    --green: #5cbf47;
    --white: #f4f4f4;
  }
  * { margin: 0; padding: 0; box-sizing: border-box; }
  html, body {
    width: 1200px;
    height: 900px;
    overflow: hidden;
    background: var(--backdrop);
  }
  .canvas {
    position: relative;
    width: 1200px;
    height: 900px;
  }
  .card {
    position: absolute;
    left: 250px;
    width: 700px;
    height: 400px;
    background: var(--card);
    overflow: hidden;
  }
  .card::after {
    content: "";
    position: absolute;
    left: 0; right: 0; bottom: 0;
    height: 12px;
    background: var(--green);
  }
  .card--front { top: 30px; }
  .card--back { top: 470px; }

  /* Front */
  .brand-mark {
    position: absolute;
    top: 70px;
    left: 0; right: 0;
    display: flex;
    justify-content: center;
    align-items: center;
    gap: 12px;
  }
  .brand-mark__square {
    width: 26px;
    height: 26px;
    background: var(--green);
  }
  .brand-mark__name {
    font-family: "Teko", sans-serif;
    font-weight: 600;
    font-size: 54px;
    line-height: 1;
    padding-top: 8px;
    color: var(--green);
    letter-spacing: 4px;
  }
  .company-name {
    position: absolute;
    top: 190px;
    left: 0; right: 0;
    text-align: center;
    font-family: "Teko", sans-serif;
    font-weight: 600;
    font-size: 64px;
    line-height: 1;
    letter-spacing: 9px;
    color: var(--green);
  }
  .front-website {
    position: absolute;
    bottom: 40px;
    left: 0; right: 0;
    text-align: center;
    font-family: "Teko", sans-serif;
    font-weight: 500;
    font-size: 22px;
    letter-spacing: 6px;
    color: var(--white);
  }

  /* Back */
  .identity {
    position: absolute;
    top: 140px;
    left: 40px;
    width: 310px;
    text-align: right;
  }
  .identity__name {
    font-family: "Teko", sans-serif;
    font-weight: 600;
    font-size: 50px;
    line-height: 1;
    letter-spacing: 1px;
    color: var(--white);
    white-space: nowrap;
  }
  .identity__title {
    font-family: "Arimo", sans-serif;
    font-weight: 700;
    font-size: 13px;
    letter-spacing: 2px;
    color: var(--green);
    margin-top: 2px;
  }
  .divider {
    position: absolute;
    top: 130px;
    left: 378px;
    width: 3px;
    height: 112px;
    background: var(--green);
  }
  .contact-list {
    position: absolute;
    top: 150px;
    left: 418px;
    list-style: none;
  }
  .contact-list li {
    display: flex;
    align-items: center;
    gap: 14px;
    height: 26px;
    font-family: "Arimo", sans-serif;
    font-size: 14px;
    letter-spacing: 1.5px;
    color: var(--white);
    white-space: nowrap;
  }
  .contact-list svg {
    width: 16px;
    height: 16px;
    flex: none;
  }
</style>
</head>
<body>
<main class="canvas">

  <section class="card card--front" aria-label="Card front">
    <div class="brand-mark">
      <span class="brand-mark__square"></span>
      <span class="brand-mark__name">QUELLROW</span>
    </div>
    <h1 class="company-name">QUELLROW CAPITAL</h1>
    <p class="front-website">WWW.FUNDQUELLROW.COM</p>
  </section>

  <section class="card card--back" aria-label="Card back">
    <div class="identity">
      <h2 class="identity__name">LUKAS VARENKO</h2>
      <p class="identity__title">Fund Manager</p>
    </div>
    <div class="divider"></div>
    <ul class="contact-list">
      <li>
        <svg viewBox="0 0 16 16" aria-hidden="true">
          <rect x="4" y="1" width="8" height="14" rx="1.5" fill="none" stroke="#5cbf47" stroke-width="1.3"/>
          <line x1="7" y1="12.5" x2="9" y2="12.5" stroke="#5cbf47" stroke-width="1.3"/>
        </svg>
        +1 555 284 6190
      </li>
      <li>
        <svg viewBox="0 0 16 16" aria-hidden="true">
          <rect x="1" y="3.5" width="14" height="9" fill="none" stroke="#5cbf47" stroke-width="1.3"/>
          <polyline points="1,3.5 8,9 15,3.5" fill="none" stroke="#5cbf47" stroke-width="1.3"/>
        </svg>
        www.FundQuellrow.com
      </li>
      <li>
        <svg viewBox="0 0 16 16" aria-hidden="true">
          <circle cx="8" cy="8" r="6.5" fill="none" stroke="#5cbf47" stroke-width="1.3"/>
          <ellipse cx="8" cy="8" rx="3" ry="6.5" fill="none" stroke="#5cbf47" stroke-width="1.1"/>
          <line x1="1.5" y1="8" x2="14.5" y2="8" stroke="#5cbf47" stroke-width="1.1"/>
        </svg>
        lv@FundQuellrow.com
      </li>
    </ul>
  </section>

</main>
</body>
</html>
```